KRV Cartridge chip board folding ammuniton boxes for retail sale

Design a scalable design for use with 20 round and 50 round boxes for Ammunition. The caliber will be 9mm but will need to be editable, all warnings and barcodes will need to be able to be edited also. I have attached the company logo.

**UPDATE**
Box dimensions
20rd= 2.55in long X 2.1in width X 1.25in height

50rd= 5.1in long x 2.6in width X 1.2in height

Please see the bullet picture i would like used if possible.

Target Market(s)

Quality shooting sports, self defense

Industry/Entity Type

Self Defense

Requirements
Must have
• supplied company logo design
Should not have
• any cartoons of any kind

```html
<!DOCTYPE html>
<html lang="en">
<head>
<meta charset="utf-8">
<title>KRV Cartridge – 9mm 115gr FMJ Box Panels</title>
<link href="https://fonts.googleapis.com/css2?family=Montserrat:wght@600;700;800;900&display=swap" rel="stylesheet">
<style>
  :root {
    --page: #f2f2f2;
    --black: #141414;
    --black-soft: #2c2c2c;
    --red-deep: #6a0c0d;
    --red: #8e1416;
    --red-line: #b3191c;
    --gold-light: #f0dca0;
    --gold: #c9a85a;
    --gold-dark: #9c7a32;
    --white: #ffffff;
    --panel-white: #ececec;
    --brass-light: #f7e08a;
    --brass-dark: #a77a1c;
  }
  * { box-sizing: border-box; margin: 0; padding: 0; }
  html, body { width: 1200px; height: 750px; overflow: hidden; }
  body { background: var(--page); font-family: "Montserrat", sans-serif; position: relative; }

  /* ---------- top flap ---------- */
  .top-flap {
    position: absolute; left: 240px; top: 40px;
    width: 920px; height: 150px;
    background: linear-gradient(90deg, var(--red-deep), var(--red));
    overflow: hidden;
  }
  .top-flap__band {
    position: absolute; left: 0; bottom: 0;
    width: 100%; height: 104px;
    background: var(--black);
    display: flex; flex-direction: column; align-items: center; justify-content: center;
  }
  .top-flap__brand { color: var(--white); font-weight: 900; font-size: 30px; line-height: 1; }
  .top-flap__type { color: var(--white); font-weight: 800; font-size: 15px; margin-top: 8px; line-height: 1.1; text-align: center; }

  /* ---------- side panel ---------- */
  .side-panel {
    position: absolute; left: 40px; top: 190px;
    width: 200px; height: 520px;
    background: var(--panel-white);
    overflow: hidden;
  }
  .side-panel__edge { position: absolute; left: 0; top: 0; width: 200px; height: 520px; }
  .side-panel__brand {
    position: absolute; left: 0; width: 100%; top: 140px;
    text-align: center; color: var(--black); font-weight: 900; font-size: 22px;
  }
  .side-panel__spec {
    position: absolute; left: 0; width: 100%; top: 360px;
    text-align: center; color: var(--white);
  }
  .side-panel__caliber { display: block; font-weight: 800; font-size: 26px; line-height: 1.1; }
  .side-panel__line { display: block; font-weight: 700; font-size: 12px; margin-top: 6px; line-height: 1.2; }

  /* ---------- front face ---------- */
  .box-front {
    position: absolute; left: 240px; top: 190px;
    width: 920px; height: 520px;
    overflow: hidden;
    background: linear-gradient(160deg, var(--red) 0%, var(--red-deep) 65%, #4a0b0c 100%);
  }
  .box-front__art { position: absolute; left: 0; top: 0; width: 920px; height: 520px; }
  .count-band__text {
    position: absolute; left: 0; top: 30px; width: 100%;
    text-align: center; color: var(--white);
    font-weight: 700; font-size: 26px; letter-spacing: 0.42em;
  }
  .brand-name {
    position: absolute; left: 0; width: 100%; top: 104px;
    text-align: center; color: var(--black); font-weight: 900; font-size: 42px;
  }
  .headline {
    position: absolute; left: 0; width: 100%; top: 162px;
    text-align: center; font-weight: 800; line-height: 1;
    background: linear-gradient(180deg, var(--gold-light) 0%, var(--gold) 55%, var(--gold-dark) 100%);
    -webkit-background-clip: text; background-clip: text; color: transparent;
  }
  .headline__line { display: block; font-size: 52px; }
  .headline__sub {
    position: absolute; left: 0; width: 100%; top: 330px;
    text-align: center; color: var(--gold); font-weight: 700; font-size: 18px;
  }
  .spec-band {
    position: absolute; left: 60px; top: 385px;
    width: 800px; height: 125px;
    display: flex; align-items: center; padding-left: 90px;
  }
  .bullet {
    width: 40px; height: 90px;
    border-radius: 20px 20px 3px 3px;
    background: linear-gradient(90deg, var(--brass-dark), var(--brass-light) 45%, var(--brass-dark));
    margin-right: 30px;
  }
  .caliber { color: var(--gold-light); font-weight: 800; line-height: 0.95; }
  .caliber__size { display: block; font-size: 52px; }
  .caliber__weight { display: block; font-size: 32px; }
  .spec-divider { width: 2px; height: 78px; background: var(--gold); margin: 0 34px; }
  .bullet-type { color: var(--gold-light); font-weight: 800; }
  .bullet-type__name { display: block; font-size: 36px; line-height: 1; }
  .bullet-type__note { display: block; font-size: 18px; margin-top: 6px; color: var(--gold); }
</style>
</head>
<body>
  <section class="top-flap">
    <div class="top-flap__band">
      <p class="top-flap__brand">KRV Cartridge</p>
      <p class="top-flap__type">FULL METAL JACKET<br>FMJ | ELITE AMMUNITION</p>
    </div>
  </section>

  <aside class="side-panel">
    <svg class="side-panel__edge" viewBox="0 0 200 520" aria-hidden="true">
      <polygon points="0,0 12,0 24,330 200,330 200,520 0,520" fill="var(--black)"/>
    </svg>
    <p class="side-panel__brand">KRV Cartridge</p>
    <p class="side-panel__spec">
      <span class="side-panel__caliber">9mm 115gr</span>
      <span class="side-panel__line">FULL METAL JACKET<br>FMJ / ELITE AMMUNITION</span>
    </p>
  </aside>

  <main class="box-front">
    <svg class="box-front__art" viewBox="0 0 920 520" aria-hidden="true">
      <polygon points="0,0 920,0 920,70 0,100" fill="var(--black)"/>
      <line x1="0" y1="430" x2="920" y2="230" stroke="var(--red-line)" stroke-width="5"/>
      <polygon points="60,395 880,380 850,510 90,515" fill="var(--black)"/>
    </svg>

    <p class="count-band__text">50 CARTRIDGES PER BOX</p>
    <p class="brand-name">KRV Cartridge</p>

    <h1 class="headline">
      <span class="headline__line">ELITE</span>
      <span class="headline__line">PERFORMANCE</span>
      <span class="headline__line">AMMUNITION</span>
    </h1>
    <p class="headline__sub">CENTERFIRE CARTRIDGES</p>

    <section class="spec-band">
      <div class="bullet" role="img" aria-label="Brass 9mm full metal jacket cartridge"></div>
      <p class="caliber">
        <span class="caliber__size">9mm</span>
        <span class="caliber__weight">115gr</span>
      </p>
      <div class="spec-divider"></div>
      <p class="bullet-type">
        <span class="bullet-type__name">FULL METAL JACKET</span>
        <span class="bullet-type__note">FMJ / ELITE AMMUNITION</span>
      </p>
    </section>
  </main>
</body>
</html>
```